Web Developer Needs a Business Card Design

I need a personal business card design that represents me as a web developer for potential employers. I would like the background to be a dark color on the front for contrast with my logo and name. The back will have all my information along with a smaller version of the logo. I want something with a modern look and feel, not too conservative. This will be used for potential employers and freelance work.

Industry/Entity Type

Business

Contact Information for Business Card

Front should have my logo and name. The back should have all my personal information which would include: name: Tom Varulek, phone: 570-614-3098, email: tomvarulek@quillbox.net, website url: www.tomvarulek.net, logo, web developer.

Font styles to use
Sans Serif

Requirements
Must have
• Must include my logo. The color palette base color will be the logo color.

```html
<!DOCTYPE html>
<html lang="en">
<head>
<meta charset="utf-8">
<title>Tom Varulek – Business Card</title>
<link rel="stylesheet" href="https://fonts.googleapis.com/css2?family=Lato:wght@400;700&display=swap">
<style>
  :root {
    --stage: #161616;
    --paper: #ffffff;
    --teal: #4cb89a;
    --teal-deep: #2a8f76;
    --ink: #222222;
    --band-dark: #333333;
    --back-card: #1c1312;
    --white: #ffffff;
  }
  * { margin: 0; padding: 0; box-sizing: border-box; }
  html, body { width: 1200px; height: 1086px; overflow: hidden; }
  body { background: var(--stage); font-family: "Lato", sans-serif; position: relative; }

  .card { position: absolute; left: 254px; width: 678px; height: 387px; border-radius: 8px; overflow: hidden; }
  .card-front { top: 126px; background: var(--paper); }
  .card-back { top: 588px; background: var(--back-card); }

  .brand-ring { position: absolute; border-radius: 50%; border: 10px solid var(--teal); }
  .card-front .brand-ring { left: 132px; top: 107px; width: 128px; height: 128px; }
  .brand-name {
    position: absolute; left: 46px; width: 300px; top: 246px;
    text-align: center; font-weight: 700; font-size: 33px; color: var(--teal); letter-spacing: 0.2px;
    white-space: nowrap;
  }

  .divider { position: absolute; left: 337px; top: 110px; width: 2px; height: 172px; background: var(--ink); }
  .divider::before { content: ""; position: absolute; left: 0; top: 0; width: 2px; height: 48px; background: var(--teal); }

  .person { position: absolute; left: 365px; top: 108px; }
  .person-name { font-weight: 700; font-size: 27px; color: var(--teal); line-height: 32px; }
  .person-role { font-size: 21px; color: var(--ink); line-height: 26px; }

  .contacts { position: absolute; left: 363px; top: 196px; list-style: none; }
  .contacts li { display: flex; align-items: center; height: 26.5px; font-size: 21px; color: var(--ink); white-space: nowrap; }
  .contacts svg { width: 21px; height: 21px; margin-right: 7px; flex: none; }

  .footer-band { position: absolute; left: 0; bottom: 0; width: 100%; height: 25px; background: var(--band-dark); }
  .footer-band .band-fill { position: absolute; left: 0; top: 0; height: 100%; width: 574px; background: var(--teal-deep); }
  .footer-band .band-dot {
    position: absolute; left: 560px; top: -2px; width: 29px; height: 29px; border-radius: 50%;
    background: var(--teal); border: 3px solid var(--white);
  }

  .card-back .brand-ring { left: 257px; top: 108px; width: 172px; height: 172px; border-width: 13px; border-color: var(--teal-deep); }
  .back-name {
    position: absolute; left: 257px; width: 172px; top: 108px; height: 172px;
    display: flex; align-items: center; justify-content: center;
    font-weight: 700; font-size: 16px; color: var(--teal-deep); white-space: nowrap;
  }
  .back-url { position: absolute; left: 0; width: 100%; top: 340px; text-align: center; font-size: 22px; color: var(--white); letter-spacing: 0.3px; }
</style>
</head>
<body>
  <section class="card card-front">
    <div class="brand-ring"></div>
    <div class="brand-name">TOM VARULEK</div>

    <div class="divider"></div>

    <div class="person">
      <div class="person-name">Tom Varulek</div>
      <div class="person-role">Web Developer</div>
    </div>

    <ul class="contacts">
      <li>
        <svg viewBox="0 0 24 24" aria-hidden="true"><path fill="#4cb89a" d="M3 9c0-3 4-4 9-4s9 1 9 4v2h-5V9H8v2H3z"/><path fill="#4cb89a" d="M6 12h12l2 7H4z"/></svg>
        570-614-3098
      </li>
      <li>
        <svg viewBox="0 0 24 24" aria-hidden="true"><rect x="2" y="5" width="20" height="14" fill="#4cb89a"/><path d="M2 5l10 8 10-8M2 19l7-7M22 19l-7-7" stroke="#fff" stroke-width="1.6" fill="none"/></svg>
        tomvarulek@quillbox.net
      </li>
      <li>
        <svg viewBox="0 0 24 24" aria-hidden="true" fill="none" stroke="#4cb89a" stroke-width="1.6"><circle cx="12" cy="12" r="10"/><ellipse cx="12" cy="12" rx="4.5" ry="10"/><path d="M2 12h20M4 7h16M4 17h16"/></svg>
        www.tomvarulek.net
      </li>
    </ul>

    <div class="footer-band">
      <div class="band-fill"></div>
      <div class="band-dot"></div>
    </div>
  </section>

  <section class="card card-back">
    <div class="brand-ring"></div>
    <div class="back-name">TOM VARULEK</div>
    <div class="back-url">www.tomvarulek.net</div>
  </section>
</body>
</html>
```